Cutting Edge Cloud Hosting Provider needs business card design

We are a new Cloud Hosting Provider called Velkari Hosting. (Velkari means cloudy in Spanish.) We provide clients with virtual resources and not virtual machines directly. Our clients purchase the resources that they will use (RAM,CPU, Hard drive space) then use those resources in as many virtual machines as they like.

We are looking for a business card design that is cutting edge and hip.
Updates

The name of the company is "Velkari Hosting". Please include the "Hosting" part of our name in the design.

Thanks

Target Market(s)

21-35 developers and I.T. Staff

Industry/Entity Type

Business

Requirements
Must have
• Rounded corners, Must Incorporate our logo, individual's name must be prominent

```html
<!DOCTYPE html>
<html lang="en">
<head>
<meta charset="utf-8">
<title>Velkari Hosting – Business Card</title>
<link rel="stylesheet" href="https://fonts.googleapis.com/css2?family=Michroma&display=swap">
<style>
  :root {
    --page-bg: #e6e9ee;
    --blue-deep: #1f6fc4;
    --blue-mid: #3b8fdc;
    --blue-light: #7fbdf0;
    --blue-pale: #a9d3f5;
    --ink-blue: #1d5aa8;
    --white: #ffffff;
    --paper: #fbfcfd;
    --line-tint: #dfeaf2;
  }
  * { box-sizing: border-box; margin: 0; padding: 0; }
  html, body { width: 1200px; height: 900px; overflow: hidden; }
  body {
    background: var(--page-bg);
    font-family: "Michroma", "Arial", sans-serif;
    display: flex;
    flex-direction: column;
    align-items: center;
    justify-content: center;
    gap: 56px;
  }
  .card {
    position: relative;
    width: 580px;
    height: 331px;
    border-radius: 16px;
    overflow: hidden;
    box-shadow: 0 6px 18px rgba(20, 40, 70, 0.18);
  }

  /* Back of card */
  .card--back {
    background: linear-gradient(160deg, var(--blue-light) 0%, var(--blue-mid) 45%, var(--blue-deep) 100%);
  }
  .card--back .texture {
    position: absolute;
    top: 0; left: 0;
    width: 100%; height: 60%;
    background: radial-gradient(ellipse at 70% 10%, rgba(255,255,255,0.35), rgba(255,255,255,0) 65%);
  }
  .card--back .brand {
    position: absolute;
    top: 118px; left: 0; right: 0;
    text-align: center;
    color: var(--white);
    font-size: 40px;
    letter-spacing: 1px;
  }
  .card--back .web {
    position: absolute;
    bottom: 30px; left: 0; right: 0;
    text-align: center;
    color: var(--white);
    font-size: 13px;
    letter-spacing: 6px;
  }

  /* Front of card */
  .card--front { background: var(--blue-mid); }
  .front-header {
    position: absolute;
    top: 0; left: 0; right: 0;
    height: 128px;
    background: var(--paper);
  }
  .front-header .texture {
    position: absolute;
    top: 0; right: 0;
    width: 52%; height: 100%;
    background: radial-gradient(ellipse at 30% 100%, var(--line-tint), rgba(255,255,255,0) 70%);
  }
  .front-header .brand {
    position: absolute;
    top: 48px; left: 36px;
    color: var(--ink-blue);
    font-size: 26px;
  }
  .front-body {
    position: absolute;
    top: 128px; left: 0; right: 0; bottom: 0;
    background: linear-gradient(180deg, var(--blue-mid) 0%, var(--blue-deep) 100%);
  }
  .front-body .band {
    position: absolute;
    left: 0; right: 0; bottom: 0;
    height: 30px;
    background: linear-gradient(180deg, rgba(169,211,245,0.35), rgba(169,211,245,0.6));
  }
  .person { position: absolute; top: 40px; left: 36px; color: var(--white); }
  .person__name { font-size: 19px; letter-spacing: 0.5px; }
  .person__title { font-size: 10px; margin-top: 4px; letter-spacing: 0.5px; }
  .person__web { font-size: 11px; margin-top: 30px; letter-spacing: 0.5px; }
  .divider {
    position: absolute;
    top: 34px; left: 340px;
    width: 1px; height: 120px;
    background: rgba(255,255,255,0.75);
  }
  .contacts {
    position: absolute;
    top: 40px; left: 356px;
    list-style: none;
    color: var(--white);
    font-size: 11px;
    line-height: 2.3;
    letter-spacing: 0.5px;
  }
</style>
</head>
<body>
  <section class="card card--back" aria-label="Business card back">
    <div class="texture" role="img" aria-label="Soft decorative wave line pattern"></div>
    <div class="brand">Velkari Hosting</div>
    <div class="web">WWW.VELKARI.COM</div>
  </section>

  <section class="card card--front" aria-label="Business card front">
    <div class="front-header">
      <div class="texture" role="img" aria-label="Faint decorative wave line pattern"></div>
      <div class="brand">Velkari Hosting</div>
    </div>
    <div class="front-body">
      <div class="band"></div>
      <div class="person">
        <div class="person__name">MARCO IBARRA</div>
        <div class="person__title">VICE-PRESIDENT</div>
        <div class="person__web">W: WWW.VELKARI.COM</div>
      </div>
      <div class="divider"></div>
      <ul class="contacts">
        <li>P. 210.555.0142</li>
        <li>C. 210.555.0187</li>
        <li>E: MARCO@VELKARI.COM</li>
      </ul>
    </div>
  </section>
</body>
</html>
```